Building company buisness cards

We are looking for a sharp modern new look for our business cards.
We are a New Zealand based company that specialises in house and land packages.
We have attached a photo of the current logo and would like to see if it can be improved somehow if needed.
We are open to any colours but we have chosen green at this stage.
Feel free to change the font and make the logo smarter looking.
Play with the colours and see what looks best.

We want a card that looks so good know one will want to throw it away!

Target Market(s)

Home buyers

Industry/Entity Type

Building

Contact Information for Business Card

Derek Tolvane
0217394062
dtolvane@quillmarkhomesteads.co.nz
quillmarkhomesteads.co.nz

Font styles to use
Serif
Sans Serif

Colors

Designer to choose colors to be used in the design.

Requirements
Must have
• Logo and company name on one side, details on the other side
Nice to have
• Color codes for the original green are HEX #4a8028, RGB(74,128,40), CMYK(42,0,69,50)
• Round corners, Raised and/or spot UV

```html
<!DOCTYPE html>
<html lang="en">
<head>
<meta charset="utf-8">
<title>Quillmark Homesteads – Business Card</title>
<link href="https://fonts.googleapis.com/css2?family=Open+Sans:wght@400;800&display=swap" rel="stylesheet">
<style>
  :root {
    --bg: #e9e7e3;
    --card-white: #ffffff;
    --card-mist: #f1f1f1;
    --grey-light: #6a6a6a;
    --grey-dark: #353535;
    --brand-green: #169a22;
    --ink: #1d1d1d;
    --ink-soft: #2e2e2e;
  }
  html, body {
    margin: 0;
    width: 1200px;
    height: 1024px;
    overflow: hidden;
    background: var(--bg);
  }
  .canvas {
    position: relative;
    width: 1200px;
    height: 1024px;
    display: flex;
    flex-direction: column;
    align-items: center;
    justify-content: center;
    gap: 32px;
  }
  .card {
    position: relative;
    width: 840px;
    height: 480px;
    border-radius: 14px;
    overflow: hidden;
    box-shadow: 0 6px 18px rgba(0,0,0,0.18);
    background: linear-gradient(180deg, var(--card-white), var(--card-mist));
  }
  .card-art {
    position: absolute;
    inset: 0;
  }
  .logo {
    position: absolute;
    left: 150px;
    top: 170px;
    display: flex;
    align-items: center;
    gap: 14px;
  }
  .logo-mark {
    width: 22px;
    height: 22px;
    background: var(--brand-green);
    flex: none;
  }
  .logo-name {
    font-family: "Open Sans", sans-serif;
    font-weight: 800;
    font-size: 46px;
    line-height: 0.98;
    letter-spacing: -1px;
    color: var(--brand-green);
  }
  .holder-name {
    position: absolute;
    right: 90px;
    top: 70px;
    font-family: "Open Sans", sans-serif;
    font-weight: 400;
    font-size: 30px;
    color: var(--ink);
  }
  .contact-list {
    position: absolute;
    right: 36px;
    top: 290px;
    margin: 0;
    padding: 0;
    list-style: none;
    font-family: "Open Sans", sans-serif;
    font-size: 21px;
    color: var(--ink-soft);
  }
  .contact-list li {
    display: flex;
    justify-content: flex-end;
    align-items: center;
    gap: 14px;
    height: 32px;
  }
  .contact-icon {
    width: 20px;
    height: 20px;
    flex: none;
  }
</style>
</head>
<body>
<main class="canvas">

  <section class="card card-front" aria-label="Business card front">
    <svg class="card-art" viewBox="0 0 840 480" aria-hidden="true">
      <defs>
        <linearGradient id="greyBand" x1="0" y1="0" x2="1" y2="1">
          <stop offset="0" stop-color="var(--grey-light)"/>
          <stop offset="1" stop-color="var(--grey-dark)"/>
        </linearGradient>
      </defs>
      <rect x="0" y="0" width="360" height="480" fill="url(#greyBand)"/>
      <circle cx="372" cy="250" r="330" fill="var(--brand-green)"/>
      <circle cx="400" cy="240" r="330" fill="var(--card-white)"/>
      <rect x="400" y="0" width="440" height="480" fill="var(--card-white)"/>
      <line x1="190" y1="292" x2="290" y2="292" stroke="#cfcfcf" stroke-width="1.5"/>
    </svg>

    <div class="logo">
      <span class="logo-mark"></span>
      <span class="logo-name">quillmark<br>homesteads.</span>
    </div>

    <p class="holder-name">Derek Tolvane</p>

    <ul class="contact-list">
      <li>0217394062
        <svg class="contact-icon" viewBox="0 0 20 20" aria-label="Phone">
          <rect width="20" height="20" fill="var(--brand-green)"/>
          <path d="M6 4 l2.5 0 1 3-1.6 1.2 a7 7 0 0 0 3.9 3.9 l1.2-1.6 3 1 0 2.5 a1.5 1.5 0 0 1-1.5 1.5 A10 10 0 0 1 4.5 5.5 1.5 1.5 0 0 1 6 4z" fill="#fff"/>
        </svg>
      </li>
      <li>dtolvane@quillmarkhomesteads.co.nz
        <svg class="contact-icon" viewBox="0 0 20 20" aria-label="Email">
          <rect width="20" height="20" fill="var(--brand-green)"/>
          <rect x="4" y="6" width="12" height="8.5" fill="none" stroke="#fff" stroke-width="1.5"/>
          <path d="M4 6 l6 5 6-5" fill="none" stroke="#fff" stroke-width="1.5"/>
        </svg>
      </li>
      <li>quillmarkhomesteads.co.nz
        <svg class="contact-icon" viewBox="0 0 20 20" aria-label="Website">
          <rect width="20" height="20" fill="var(--brand-green)"/>
          <circle cx="10" cy="10" r="5.5" fill="none" stroke="#fff" stroke-width="1.5"/>
          <path d="M4.5 10 h11 M10 4.5 c-3 3-3 8 0 11 M10 4.5 c3 3 3 8 0 11" fill="none" stroke="#fff" stroke-width="1.2"/>
        </svg>
      </li>
    </ul>
  </section>

  <section class="card card-back" aria-label="Business card back">
    <svg class="card-art" viewBox="0 0 840 480" aria-hidden="true">
      <defs>
        <linearGradient id="greyBack" x1="0" y1="0" x2="1" y2="1">
          <stop offset="0" stop-color="var(--grey-light)"/>
          <stop offset="1" stop-color="var(--grey-dark)"/>
        </linearGradient>
      </defs>
      <rect width="840" height="480" fill="url(#greyBack)"/>
      <circle cx="400" cy="250" r="300" fill="var(--brand-green)"/>
      <circle cx="420" cy="240" r="300" fill="var(--card-white)"/>
    </svg>
  </section>

</main>
</body>
</html>
```